Heritage Hollow Business Cards

Require a business card design. <br/><br/>Needs to include logo (either round or long version) plus these details:<br/>Maya Torvell<br/>Heritage Hollow<br/>maya@kelvadtrading.com.au<br/>02 6481 7395<br/>PO Box Glenwarra NSW 2791<br/>www.heritagehollow.com.au<br/><br/>I need in an editable format so that I can create for multiple staff members. <br/><br/>

Target Market(s)

We are an online store selling renovation products to home owners are builders. Looking for a classic classy design.

Industry/Entity Type

Home And Garden

Contact Information for Business Card

Maya Torvell
Heritage Hollow
maya@kelvadtrading.com.au
02 6481 7395
PO Box Glenwarra NSW 2791
www.heritagehollow.com.au

Colors

Designer to choose colors to be used in the design.

Requirements
Must have
• Must include Logo.

```html
<!DOCTYPE html>
<html lang="en">
<head>
<meta charset="utf-8">
<title>Heritage Hollow Business Cards</title>
<link rel="stylesheet" href="https://fonts.googleapis.com/css2?family=Work+Sans:wght@400;500;700&family=Alegreya:wght@500&display=swap">
<style>
  :root {
    --bg: #e4e4e4;
    --card-dark: #1b1b1b;
    --card-light: #ffffff;
    --ink: #1e1e1e;
    --ink-soft: #8a8a8a;
    --ink-mid: #444444;
    --on-dark: #f2f2f2;
    --rule: #2a2a2a;
  }
  * { box-sizing: border-box; margin: 0; padding: 0; }
  html, body { width: 1200px; height: 930px; overflow: hidden; }
  body {
    background: var(--bg);
    font-family: "Work Sans", sans-serif;
    position: relative;
  }
  .card {
    position: absolute;
    left: 300px;
    width: 600px;
    height: 345px;
    border-radius: 22px;
    box-shadow: 0 6px 18px rgba(0,0,0,0.18);
  }
  .card--back { top: 95px; background: var(--card-dark); color: var(--on-dark); }
  .card--front { top: 490px; background: var(--card-light); color: var(--ink); }

  .brand-mark {
    position: absolute;
    border-radius: 50%;
    display: flex;
    align-items: center;
    justify-content: center;
    text-align: center;
    font-family: "Alegreya", serif;
    font-weight: 500;
    line-height: 1.05;
  }
  .card--back .brand-mark {
    left: 210px; top: 40px; width: 180px; height: 180px;
    border: 1px solid var(--on-dark);
    font-size: 30px;
    color: var(--on-dark);
  }
  .back-url {
    position: absolute;
    left: 0; right: 0; bottom: 42px;
    text-align: center;
    font-size: 15px;
    letter-spacing: 0.32em;
    color: var(--on-dark);
  }
  .back-url strong { font-weight: 700; }

  .card--front .brand-mark {
    left: 56px; top: 88px; width: 170px; height: 170px;
    border: 1px solid var(--ink-mid);
    font-size: 28px;
    color: var(--ink);
  }
  .divider {
    position: absolute;
    left: 262px; top: 70px;
    width: 1.5px; height: 210px;
    background: var(--rule);
  }
  .details { position: absolute; left: 292px; top: 62px; }
  .person-name { font-size: 25px; font-weight: 700; letter-spacing: 0.02em; }
  .person-role { font-size: 14px; color: var(--ink-soft); margin-top: 2px; }
  .company { font-size: 15px; color: var(--ink); margin-top: 6px; }
  .address { font-size: 15px; color: var(--ink-soft); line-height: 1.3; margin-top: 4px; }
  .contact-list { list-style: none; margin-top: 6px; }
  .contact-list li {
    display: flex; align-items: center; gap: 10px;
    font-size: 15px; color: var(--ink-soft); line-height: 1.4;
  }
  .contact-list li.web { color: var(--ink-mid); }
  .contact-list svg { width: 13px; height: 13px; flex: none; }
</style>
</head>
<body>
  <section class="card card--back" aria-label="Card back">
    <div class="brand-mark">Heritage<br>Hollow</div>
    <p class="back-url">www.<strong>heritagehollow</strong>.com.au</p>
  </section>

  <section class="card card--front" aria-label="Card front">
    <div class="brand-mark">Heritage<br>Hollow</div>
    <div class="divider"></div>
    <div class="details">
      <h1 class="person-name">Maya Torvell</h1>
      <p class="person-role">Director</p>
      <p class="company">Heritage Hollow</p>
      <p class="address">PO Box Glenwarra<br>NSW 2791</p>
      <ul class="contact-list">
        <li>
          <svg viewBox="0 0 16 16" aria-hidden="true"><path fill="#1e1e1e" d="M3.5 1l2.5 3-1.5 2c1 2 3 4 5 5l2-1.5 3 2.5-1.5 2.5C7 14.5 1.5 9 1 2.5z"/></svg>
          02 6481 7395
        </li>
        <li>
          <svg viewBox="0 0 16 16" aria-hidden="true"><rect x="1" y="3" width="14" height="10" rx="1" fill="none" stroke="#1e1e1e" stroke-width="1.6"/><path d="M1.5 4l6.5 5 6.5-5" fill="none" stroke="#1e1e1e" stroke-width="1.6"/></svg>
          maya@kelvadtrading.com.au
        </li>
        <li class="web">
          <svg viewBox="0 0 16 16" aria-hidden="true"><circle cx="8" cy="8" r="7" fill="#1e1e1e"/><path d="M1 8h14M8 1c-3 3.5-3 10.5 0 14M8 1c3 3.5 3 10.5 0 14" fill="none" stroke="#fff" stroke-width="1"/></svg>
          www.heritagehollow.com.au
        </li>
      </ul>
    </div>
  </section>
</body>
</html>
```